Modern Business Card

Modern professional business card with more than just logo and demographic info. Something memorable.

We are a trendy/modern chiropractic group with an emphasis on neurology, hence the minimalist-type brain logo. We want to convey that modern and technical aspect with professionalism and the elite nature of our practice environment.

```html
<!DOCTYPE html>
<html lang="en">
<head>
<meta charset="utf-8">
<title>Kestrel Chiropractic — Business Card</title>
<link rel="stylesheet" href="https://fonts.googleapis.com/css2?family=Open+Sans:wght@400;600;700&display=swap">
<style>
  :root {
    --backdrop: #8a8a8a;
    --card: #ffffff;
    --brand-blue: #417bc2;
    --brand-blue-deep: #3a6fb0;
    --ink: #1a1a1a;
    --ink-soft: #3a3a3a;
    --rule: #111111;
  }
  * { box-sizing: border-box; margin: 0; padding: 0; }
  html, body {
    width: 1200px; height: 900px; overflow: hidden;
    background: radial-gradient(circle at 50% 50%, #a4a4a4 0%, var(--backdrop) 55%, #6a6a6a 100%);
    font-family: "Open Sans", Arial, sans-serif;
  }
  .stage {
    position: relative; width: 1200px; height: 900px;
    display: flex; flex-direction: column; align-items: center; justify-content: center; gap: 60px;
  }
  .card {
    position: relative; width: 525px; height: 300px;
    background: var(--card); border-radius: 14px; overflow: hidden;
    box-shadow: 0 10px 28px rgba(0,0,0,.35);
  }

  /* Brand side */
  .card--brand .brand-band {
    position: absolute; left: 0; right: 0; top: 62px; height: 124px;
    background: linear-gradient(100deg, var(--brand-blue-deep), #4a86cc 50%, var(--brand-blue-deep));
    display: flex; align-items: center; justify-content: center; gap: 14px;
  }
  .brand-mark { width: 22px; height: 22px; background: #ffffff; flex: none; }
  .brand-name {
    color: #ffffff; font-weight: 600; font-size: 30px; letter-spacing: 2px; text-transform: uppercase;
    white-space: nowrap;
  }
  .card--brand .web-rule {
    position: absolute; left: 0; right: 0; top: 226px;
    display: flex; align-items: center; gap: 14px;
  }
  .web-rule .line { flex: 1; height: 1px; background: var(--brand-blue); }
  .web-rule .web { color: var(--brand-blue); font-size: 14px; }

  /* Contact side */
  .card--contact .name-tab {
    position: absolute; left: 0; top: 36px; width: 8px; height: 28px; background: var(--brand-blue);
  }
  .person { position: absolute; left: 34px; top: 30px; }
  .person-name { font-size: 26px; color: var(--ink); letter-spacing: .3px; line-height: 1.1; white-space: nowrap; }
  .person-name strong { font-weight: 700; }
  .person-role { font-size: 13px; color: var(--ink-soft); letter-spacing: .5px; margin-top: 2px; }
  .divider { position: absolute; left: 28px; right: 60px; top: 100px; height: 2px; display: flex; }
  .divider .lead { width: 150px; height: 3px; margin-top: -1px; background: var(--brand-blue); }
  .divider .rest { flex: 1; height: 1px; background: var(--rule); }
  .card-logo {
    position: absolute; right: 34px; top: 126px;
    display: flex; align-items: center; gap: 10px;
  }
  .card-logo .brand-mark { width: 16px; height: 16px; background: var(--brand-blue); }
  .card-logo .brand-name { color: var(--ink); font-size: 18px; letter-spacing: 1.5px; }
  .contacts { position: absolute; left: 30px; top: 124px; display: flex; flex-direction: column; gap: 14px; }
  .contact-row { display: flex; align-items: center; gap: 12px; font-size: 14px; color: var(--ink); }
  .icon-tile {
    width: 24px; height: 24px; border-radius: 4px; background: var(--brand-blue); flex: none;
    display: flex; align-items: center; justify-content: center;
  }
  .address {
    position: absolute; right: 34px; top: 200px;
    display: flex; align-items: flex-start; gap: 12px;
  }
  .address-text { font-size: 16px; color: var(--ink); line-height: 1.45; text-align: left; }
  .contact-band { position: absolute; left: 0; right: 0; bottom: 0; height: 20px; background: var(--brand-blue); }
</style>
</head>
<body>
<main class="stage">
  <section class="card card--brand" aria-label="Business card, brand side">
    <div class="brand-band">
      <span class="brand-mark" aria-hidden="true"></span>
      <span class="brand-name">Kestrel Chiropractic</span>
    </div>
    <div class="web-rule">
      <span class="line"></span>
      <span class="web">www.domainname.com</span>
      <span class="line"></span>
    </div>
  </section>

  <section class="card card--contact" aria-label="Business card, contact side">
    <span class="name-tab" aria-hidden="true"></span>
    <div class="person">
      <p class="person-name"><strong>DANIEL</strong> REYES</p>
      <p class="person-role">FOUNDER &amp; CEO</p>
    </div>
    <div class="divider" aria-hidden="true"><span class="lead"></span><span class="rest"></span></div>

    <div class="contacts">
      <p class="contact-row">
        <span class="icon-tile">
          <svg width="12" height="14" viewBox="0 0 12 14" aria-hidden="true"><rect x="2" y="1" width="8" height="12" rx="1.5" fill="none" stroke="#fff" stroke-width="1.4"/><circle cx="6" cy="10.5" r=".9" fill="#fff"/></svg>
        </span>
        012-345-6789
      </p>
      <p class="contact-row">
        <span class="icon-tile">
          <svg width="14" height="14" viewBox="0 0 14 14" aria-hidden="true"><circle cx="3" cy="11" r="1.4" fill="#fff"/><path d="M2 7a5 5 0 0 1 5 5M2 3a9 9 0 0 1 9 9" fill="none" stroke="#fff" stroke-width="1.5"/></svg>
        </span>
        www.domainname.com
      </p>
    </div>

    <div class="card-logo">
      <span class="brand-mark" aria-hidden="true"></span>
      <span class="brand-name">Kestrel Chiropractic</span>
    </div>

    <div class="address">
      <span class="icon-tile">
        <svg width="12" height="14" viewBox="0 0 12 14" aria-hidden="true"><path d="M6 13S1.5 8 1.5 5.2a4.5 4.5 0 0 1 9 0C10.5 8 6 13 6 13z" fill="#fff"/><circle cx="6" cy="5.2" r="1.6" fill="#417bc2"/></svg>
      </span>
      <p class="address-text">Address, Suit, Floor<br>City, Country, Zipcode</p>
    </div>
    <span class="contact-band" aria-hidden="true"></span>
  </section>
</main>
</body>
</html>
```